Garden Design Flier

I would like a PDF of this half page A4 flier in soft green tones with dark green leaves.

Target Market(s)

Home owners and real estate agents

Font styles to use
Serif
Other font styles liked:
• Papyrus

Colors
acd136
9bcb3c
cadf82
fefdec

Requirements
Must have
• Green tones
Nice to have
• Leaves, vines, lawns
Should not have
• Open to ideas, but classic style

```html
<!DOCTYPE html>
<html lang="en">
<head>
<meta charset="utf-8">
<title>Verdure Gardens – Flier</title>
<link rel="stylesheet" href="https://fonts.googleapis.com/css2?family=Marcellus&family=Crimson+Pro:wght@400;500&display=swap">
<style>
  :root {
    --backdrop: #5f5f5f;
    --sky: #dfe9e7;
    --leaf-light: #9fd06a;
    --leaf-mid: #6fb548;
    --leaf-dark: #2f7a2a;
    --panel: #8bc35f;
    --band: #c0d998;
    --frame: rgba(235, 242, 238, 0.55);
    --ink: #101a2e;
  }
  * { margin: 0; padding: 0; box-sizing: border-box; }
  html, body { width: 1040px; height: 1200px; overflow: hidden; }
  body {
    background: var(--backdrop);
    font-family: "Crimson Pro", Georgia, serif;
    color: var(--ink);
  }
  .flier {
    position: absolute;
    left: 120px; top: 33px;
    width: 800px; height: 1134px;
    overflow: hidden;
    background: var(--sky);
  }
  .foliage-photo {
    position: absolute; inset: 0;
    background:
      radial-gradient(ellipse 40% 30% at 15% 10%, var(--leaf-dark) 0%, transparent 70%),
      radial-gradient(ellipse 35% 25% at 55% 12%, var(--leaf-mid) 0%, transparent 70%),
      radial-gradient(ellipse 30% 25% at 85% 20%, var(--leaf-light) 0%, transparent 70%),
      radial-gradient(ellipse 10% 40% at 3% 60%, var(--leaf-mid) 0%, transparent 80%),
      radial-gradient(ellipse 8% 30% at 98% 55%, var(--leaf-light) 0%, transparent 80%),
      linear-gradient(180deg, #cfe3c4 0%, var(--sky) 55%, #d3e0e2 100%);
  }
  .panel-frame {
    position: absolute;
    left: 38px; top: 322px; width: 738px; height: 812px;
    background: var(--frame);
  }
  .panel {
    position: absolute;
    left: 42px; top: 333px; width: 717px; height: 801px;
    background: var(--panel);
  }
  .masthead { position: absolute; left: 0; top: 0; width: 100%; height: 310px; text-align: center; }
  .brand-name {
    position: absolute; left: 0; right: 0; top: 34px;
    font-family: "Marcellus", Georgia, serif;
    font-weight: 400;
    font-size: 120px; line-height: 1; letter-spacing: 0.03em;
  }
  .brand-sub {
    position: absolute; left: 0; right: 0; top: 160px;
    font-size: 22px; letter-spacing: 0.6em; padding-left: 0.6em;
  }
  .brand-owner { position: absolute; left: 0; right: 0; top: 188px; font-size: 19px; }
  .credential { position: absolute; left: 0; right: 0; top: 238px; font-size: 18px; line-height: 22px; }
  .services {
    position: absolute; left: 0; top: 310px; width: 100%; height: 198px;
    background: var(--band);
    display: flex; flex-direction: column; align-items: center; justify-content: center; gap: 6px;
  }
  .service-row { display: flex; align-items: center; gap: 14px; font-size: 36px; line-height: 40px; }
  .service-row svg { width: 28px; height: 30px; fill: var(--ink); margin-left: 14px; }
  .service-row svg:first-child { margin-left: 0; }
  .details { position: absolute; left: 0; top: 508px; width: 100%; height: 293px; }
  .pitch {
    position: absolute; left: 93px; top: 42px; width: 245px;
    font-size: 18px; line-height: 23px; white-space: nowrap;
  }
  .pitch p + p { margin-top: 19px; }
  .divider {
    position: absolute; left: 358px; top: 38px; height: 210px;
    border-left: 2px dotted var(--ink);
  }
  .contact { position: absolute; left: 382px; top: 104px; font-size: 18px; line-height: 27px; list-style: none; white-space: nowrap; }
</style>
</head>
<body>
  <main class="flier">
    <div class="foliage-photo" role="img" aria-label="Photograph of backlit green leaves and dark vines against a pale sky"></div>
    <div class="panel-frame"></div>
    <section class="panel">
      <header class="masthead">
        <h1 class="brand-name">VERDURE</h1>
        <div class="brand-sub">GARDENS</div>
        <div class="brand-owner">by Liam Hartwell</div>
        <div class="credential">Certificate 3, Horticulture,<br>State Trade College</div>
      </header>
      <div class="services">
        <div class="service-row">
          <svg viewBox="0 0 28 30" aria-hidden="true"><path d="M4 26C2 14 10 4 26 3c1 14-8 24-20 23z M7 24L22 8" stroke="#c0d998" stroke-width="1.6"/></svg>
          <span>DESIGN</span>
          <svg viewBox="0 0 28 30" aria-hidden="true"><path d="M4 26C2 14 10 4 26 3c1 14-8 24-20 23z M7 24L22 8" stroke="#c0d998" stroke-width="1.6"/></svg>
          <span>INSTALL</span>
        </div>
        <div class="service-row">
          <svg viewBox="0 0 28 30" aria-hidden="true"><path d="M4 26C2 14 10 4 26 3c1 14-8 24-20 23z M7 24L22 8" stroke="#c0d998" stroke-width="1.6"/></svg>
          <span>GROW</span>
          <svg viewBox="0 0 28 30" aria-hidden="true"><path d="M4 26C2 14 10 4 26 3c1 14-8 24-20 23z M7 24L22 8" stroke="#c0d998" stroke-width="1.6"/></svg>
          <span>TEND</span>
          <svg viewBox="0 0 28 30" aria-hidden="true"><path d="M4 26C2 14 10 4 26 3c1 14-8 24-20 23z M7 24L22 8" stroke="#c0d998" stroke-width="1.6"/></svg>
          <span>ENJOY</span>
        </div>
      </div>
      <div class="details">
        <div class="pitch">
          <p>All your gardening and<br>landscaping needs from<br>design and installation to<br>general maintenance</p>
          <p>Bespoke vegetable gardens<br>and potager created to suite<br>your site and requirements</p>
        </div>
        <div class="divider"></div>
        <ul class="contact">
          <li>E: liam@verduregardens.com.au</li>
          <li>M: 0400-128355</li>
          <li>ABN: 51824097316</li>
        </ul>
      </div>
    </section>
  </main>
</body>
</html>
```